National Sales - Pick Up Truck Dealer

We need a logo design for a new vehicle dealership based in Sydney, Eastmarch. The business name is Coastal Iron Haulers Motor Co. We will be selling American 'trucks/pick up trucks' like KRV, Torvan, Blaxer, Morrow T420, Kenzo Raptors, Morrow T640 and the likes.

These vehicles are a luxury option and we would like the logo to be strong, luxurious and masculine.Colours will be black and red or black and blue with the option of grey and white.

Target Market(s)

Men

Industry/Entity Type

Car Dealer

Contact Information for Business Card

Dennis Harlowe
Managing Director
0412 639 274
den@qelvtrk.com.au

Level 5, Brindle Parkway
17 Pemberly Lane
Wendlebury Hills
NWR
Eastmarch
Licence No: MD493152

Back of the card

qelvtrk.com.au

Font styles to use
Sans Serif

Colors

Designer to choose colors to be used in the design.

Requirements
Must have
• The company logo that is in the attachments, you can choose from the three which one you would like to work with. Must have vehicle images ....Please look at the attachments as they show examples of what we like and also provides potential images. If you choose to put an image on the front even if it is just the front of the vehicle can you please use the Black KRV Sorrento. Must have all details from the business card details section front and back
Nice to have
• N/A
Should not have
• No cars or standard trucks, please refer to the attached images to understand the product . Should not have any new logos or branding. No other colours besides what is in the logo you choose.

```html
<!DOCTYPE html>
<html lang="en">
<head>
<meta charset="utf-8">
<title>Coastal Iron Haulers Motor Co – Business Card</title>
<link href="https://fonts.googleapis.com/css2?family=Roboto:ital,wght@0,400;0,500;0,900;1,400&display=swap" rel="stylesheet">
<style>
  :root {
    --page-bg: #e4e4e4;
    --card-white: #ffffff;
    --brand-red: #e32237;
    --deep-red: #7a1c2a;
    --ink: #1b1b1b;
    --vehicle-dark: #2a2d33;
    --vehicle-mid: #4a4e56;
  }
  * { box-sizing: border-box; margin: 0; padding: 0; }
  html, body {
    width: 1200px; height: 835px; overflow: hidden;
    background: var(--page-bg);
    font-family: "Roboto", Arial, sans-serif;
  }
  .canvas { position: relative; width: 1200px; height: 835px; }
  .card {
    position: absolute; top: 258px;
    width: 520px; height: 318px;
    background: var(--card-white);
    box-shadow: 0 10px 30px rgba(0,0,0,0.18);
    overflow: hidden;
  }
  .card--back { left: 50px; }
  .card--front { left: 630px; }

  .brand-name {
    position: absolute;
    font-weight: 900;
    color: var(--ink);
    text-transform: uppercase;
    text-align: center;
    line-height: 1.05;
    letter-spacing: 1px;
  }
  .card--back .brand-name { left: 0; right: 0; top: 70px; font-size: 30px; }
  .card--front .brand-name { left: 30px; top: 18px; width: 300px; font-size: 22px; text-align: left; }

  .rule { position: absolute; left: 0; right: 0; height: 2px; background: var(--brand-red); }
  .rule--upper { top: 170px; }
  .rule--lower { top: 268px; }

  .website {
    position: absolute; left: 0; right: 0; top: 205px;
    text-align: center; color: var(--brand-red);
    font-weight: 500; font-size: 20px;
  }

  .front-shapes { position: absolute; inset: 0; }

  .contact-list {
    position: absolute; left: 18px; top: 122px;
    list-style: none; color: var(--card-white);
    font-size: 10px; font-weight: 500;
  }
  .contact-item { display: flex; align-items: flex-start; gap: 16px; margin-bottom: 14px; }
  .contact-item svg { flex: 0 0 18px; }
  .contact-item span { line-height: 1.35; padding-top: 3px; }

  .person { position: absolute; right: 22px; top: 128px; text-align: right; color: var(--card-white); }
  .person-name { font-weight: 900; font-size: 28px; letter-spacing: 0.5px; text-transform: uppercase; }
  .person-title { font-style: italic; font-size: 16px; margin-top: 4px; }

  .vehicle-photo {
    position: absolute; right: 40px; bottom: 14px;
    width: 150px; height: 100px; border-radius: 10px;
    background: radial-gradient(ellipse at 50% 45%, var(--vehicle-mid), var(--vehicle-dark) 70%);
  }
</style>
</head>
<body>
<main class="canvas">

  <section class="card card--back" aria-label="Card back">
    <div class="rule rule--upper"></div>
    <h2 class="brand-name">Coastal Iron Haulers<br>Motor Co</h2>
    <p class="website">qelvtrk.com.au</p>
    <div class="rule rule--lower"></div>
  </section>

  <section class="card card--front" aria-label="Card front">
    <svg class="front-shapes" width="520" height="318" viewBox="0 0 520 318">
      <polygon points="0,110 300,110 350,78 520,78 520,318 0,318" fill="var(--brand-red)"/>
      <polygon points="0,215 170,262 340,262 520,205 520,318 0,318" fill="var(--deep-red)"/>
    </svg>

    <h2 class="brand-name">Coastal Iron Haulers<br>Motor Co</h2>

    <ul class="contact-list">
      <li class="contact-item">
        <svg width="18" height="14" viewBox="0 0 18 14" fill="none" stroke="#fff" stroke-width="1.2">
          <rect x="0.6" y="0.6" width="16.8" height="12.8"/><polyline points="0.6,0.6 9,8 17.4,0.6"/>
        </svg>
        <span>den@qelvtrk.com.au</span>
      </li>
      <li class="contact-item">
        <svg width="18" height="20" viewBox="0 0 18 20" fill="none" stroke="#fff" stroke-width="1.2">
          <rect x="4" y="0.6" width="10" height="18.8" rx="1.5"/><line x1="7.5" y1="16.5" x2="10.5" y2="16.5"/>
        </svg>
        <span>0412 639 274</span>
      </li>
      <li class="contact-item">
        <svg width="18" height="20" viewBox="0 0 18 20">
          <path d="M9 0.5a6.5 6.5 0 0 0-6.5 6.5c0 4.8 6.5 12.5 6.5 12.5s6.5-7.7 6.5-12.5A6.5 6.5 0 0 0 9 0.5z" fill="#fff"/>
          <circle cx="9" cy="7" r="2.4" fill="var(--brand-red)"/>
        </svg>
        <span>Level 5, Brindle Parkway<br>17 Pemberly Lane<br>Wendlebury Hills<br>NWR<br>Eastmarch</span>
      </li>
    </ul>

    <div class="person">
      <p class="person-name">Dennis Harlowe</p>
      <p class="person-title">Managing Director</p>
    </div>

    <div class="vehicle-photo" role="img" aria-label="Front view photo of a Black KRV Sorrento pickup"></div>
  </section>

</main>
</body>
</html>
```